food delivery web site design

Currently we have a smartphone app (ios/android) that is being used by our clients to make orders to about 30 different restaurants.

We would like to extent this and have also a website that is able to mimic the same functionalities:
- register
- show restaurants based on the selected address
- make order to an restaurant
- being able to process orders for other registered users (please read the attached doc for complete info on this)

Take a look at the attached doc for more info.

```html
<!DOCTYPE html>
<html lang="ro">
<head>
<meta charset="utf-8">
<title>Gustar – Coș de cumpărături</title>
<link href="https://fonts.googleapis.com/css2?family=Oswald:wght@300;400;500&family=Open+Sans:ital,wght@0,400;1,400&display=swap" rel="stylesheet">
<style>
:root{
  --red:#9e1a0b;
  --red-dark:#7e1408;
  --ink:#2b2523;
  --gray:#8a8a8a;
  --gray-light:#c4c4c4;
  --line:#d8d8d8;
  --yellow:#f3c24a;
  --footer:#2a2626;
  --white:#fff;
}
*{box-sizing:border-box;margin:0;padding:0}
html,body{width:1114px;height:1200px;overflow:hidden;background:var(--white)}
body{position:relative;font-family:"Open Sans",sans-serif;color:var(--ink)}
.abs{position:absolute}
.pattern-strip{left:0;top:0;width:1114px;height:47px;background:linear-gradient(#f7f7f7,#ececec)}
.top-band{left:0;top:47px;width:1114px;height:50px;background:var(--red);border-top:2px solid var(--red-dark);border-bottom:2px solid var(--red-dark)}
.band-line{height:1px;background:rgba(255,255,255,.6);top:24px}
.call{left:325px;top:8px;font-family:"Oswald",sans-serif;font-size:22px;color:var(--white);letter-spacing:-.3px;display:flex;align-items:center;gap:6px}
.call .num{color:var(--yellow)}
.dots{left:566px;top:24px;width:258px;border-top:2px dotted rgba(255,255,255,.55)}
.auth{top:14px;font-family:"Oswald",sans-serif;font-size:14px;color:var(--white);display:flex;align-items:center;gap:5px}
.brand-badge{left:129px;top:0;width:145px;height:146px}
.brand-name{left:129px;top:58px;width:145px;text-align:center;font-family:"Oswald",sans-serif;font-weight:500;font-size:24px;color:var(--red)}
.order-title{font-family:"Oswald",sans-serif;font-weight:500;font-size:40px;color:var(--red);left:127px;line-height:1}
.cart-title{right:128px;top:218px;font-family:"Oswald",sans-serif;font-size:50px;color:var(--gray-light);line-height:1}
.rule{left:129px;width:857px;height:1px;background:var(--line)}
.col-head{font-size:14px;color:var(--gray);width:100px;text-align:center;margin-left:-50px}
.item{left:129px;font-family:"Oswald",sans-serif;font-size:19px;color:#6e6a68;letter-spacing:.3px}
.qty{left:489px;width:60px;height:27px;border:1px solid #c9c9c9;border-bottom:2px solid #aaa;display:flex;align-items:center;font-size:16px}
.qty b{width:19px;text-align:center;font-weight:700;color:var(--ink)}
.qty span{border-left:1px solid #ccc;padding-left:5px;color:var(--red);font-size:15px;line-height:16px}
.price{left:607px;width:100px;text-align:center;font-size:20px}
.total{left:742px;width:140px;text-align:center;font-family:"Oswald",sans-serif;font-size:40px;color:var(--red);line-height:1}
.label{font-family:"Oswald",sans-serif;font-weight:300;font-size:17px;color:var(--gray)}
.opt{left:207px;font-family:"Oswald",sans-serif;font-weight:300;font-size:17px;color:var(--ink);display:flex;align-items:center;gap:9px}
.box{width:10px;height:10px;border:1px solid #777;display:inline-block;position:relative}
.box.on::after{content:"";position:absolute;left:2px;top:2px;width:4px;height:4px;background:var(--red)}
.time{left:231px;top:887px;width:52px;height:22px;border:1px solid #aaa;background:linear-gradient(#fff,#e9e9e9);font-family:"Oswald",sans-serif;font-weight:300;font-size:16px;padding-left:4px;line-height:20px}
.notes{left:626px;top:830px;width:358px;height:111px;border:1px solid #c9c9c9;padding:7px 10px;font-style:italic;font-size:14px;line-height:21px;color:#8d8d8d}
.transport{left:129px;top:1013px;font-family:"Oswald",sans-serif;font-weight:300;font-size:23px;color:var(--gray)}
.grand{left:129px;top:1043px;font-family:"Oswald",sans-serif;font-size:37px;color:#5a5655}
.grand em{font-style:normal;color:var(--red)}
.send{left:771px;top:1019px;width:215px;height:59px;background:var(--red);color:var(--white);font-family:"Oswald",sans-serif;font-weight:500;font-size:26px;display:flex;align-items:center;justify-content:center}
.site-footer{left:0;top:1149px;width:1114px;height:51px;background:var(--footer)}
.foot-links{left:129px;top:16px;font-size:12px;color:#e8e8e8;display:flex}
.foot-links a{color:inherit;text-decoration:none;padding:0 9px;border-left:1px solid #666}
.foot-links a:first-child{padding-left:0;border-left:0}
.copy{right:128px;top:16px;font-size:12px;color:#e8e8e8}
</style>
</head>
<body>
<div class="abs pattern-strip" role="img" aria-label="Decorative pattern of line-drawn food items"></div>

<header class="abs top-band">
  <div class="abs band-line" style="left:0;width:129px"></div>
  <div class="abs band-line" style="left:274px;width:36px"></div>
  <div class="abs call">SUNĂ-NE LA
    <svg width="14" height="18" viewBox="0 0 14 18"><path d="M3 1l3 4-2 2c1 3 3 5 5 6l2-2 3 3-2 3C6 17 1 10 1 4z" fill="var(--yellow)"/></svg>
    <span class="num">0700 123 456</span></div>
  <div class="abs dots"></div>
  <div class="abs auth" style="left:840px">
    <svg width="13" height="12" viewBox="0 0 13 12"><path d="M1 11V7c0-2 2-3 4-3h3V1l5 4.5L8 10V7H5c-2 0-3 1-4 4z" fill="#fff"/></svg>LOGIN</div>
  <div class="abs auth" style="left:910px">
    <svg width="15" height="12" viewBox="0 0 15 12"><circle cx="5" cy="3.5" r="3" fill="#fff"/><path d="M0 12c0-4 2-5 5-5s5 1 5 5z M11 3h1.5v1.5H14V6h-1.5v1.5H11V6H9.5V4.5H11z" fill="#fff"/></svg>SIGN IN</div>
  <div class="abs band-line" style="left:988px;width:126px"></div>
</header>

<svg class="abs brand-badge" viewBox="0 0 145 146" aria-hidden="true">
  <path d="M1 0h143v121l-22 21H23L1 121z" fill="#1f1a19" stroke="#3a3434" stroke-width="2"/>
  <path d="M6 0h133v118l-19 19H25L6 118z" fill="none" stroke="#5a5252" stroke-width="1"/>
  <circle cx="73" cy="72" r="51" fill="#fff"/>
  <circle cx="73" cy="74" r="40" fill="#ececec"/>
</svg>
<div class="abs brand-name">Gustar</div>

<main>
  <h1 class="abs order-title" style="top:228px">NUME PRENUME 1</h1>
  <h2 class="abs cart-title">COȘ DE CUMPĂRĂTURI</h2>
  <div class="abs rule" style="top:275px"></div>

  <div class="abs col-head" style="left:518px;top:294px">Cantitate</div>
  <div class="abs col-head" style="left:657px;top:294px">Preț</div>
  <div class="abs col-head" style="left:812px;top:294px">Total</div>

  <div class="abs item" style="top:326px">ZACUSCĂ DE VINETE</div>
  <div class="abs qty" style="top:327px"><b>+</b><b>-</b><span>3</span></div>
  <div class="abs price" style="top:325px">33 Lei</div>
  <div class="abs total" style="top:319px">85 LEI</div>

  <div class="abs item" style="top:388px">FASOLE BĂTUTĂ</div>
  <div class="abs qty" style="top:389px"><b>+</b><b>-</b><span>3</span></div>
  <div class="abs price" style="top:387px">33 Lei</div>

  <div class="abs item" style="top:450px">SALATĂ ISACCEA</div>
  <div class="abs qty" style="top:451px"><b>+</b><b>-</b><span>1</span></div>
  <div class="abs price" style="top:449px">19 Lei</div>

  <div class="abs rule" style="top:515px"></div>

  <h1 class="abs order-title" style="top:571px">NUME PRENUME 2</h1>
  <div class="abs rule" style="top:618px"></div>

  <div class="abs col-head" style="left:518px;top:639px">Cantitate</div>
  <div class="abs col-head" style="left:657px;top:639px">Preț</div>
  <div class="abs col-head" style="left:812px;top:639px">Total</div>

  <div class="abs item" style="top:671px">SALATĂ DE ICRE DE CRAP</div>
  <div class="abs qty" style="top:672px"><b>+</b><b>-</b><span>1</span></div>
  <div class="abs price" style="top:670px">16 Lei</div>
  <div class="abs total" style="top:664px">28 LEI</div>

  <div class="abs item" style="top:733px">SLĂNINĂ AFUMATĂ (50GR)</div>
  <div class="abs qty" style="top:734px"><b>+</b><b>-</b><span>4</span></div>
  <div class="abs price" style="top:732px">12 Lei</div>

  <div class="abs rule" style="top:788px"></div>

  <div class="abs label" style="left:129px;top:825px">LIVRARE:</div>
  <div class="abs opt" style="top:825px"><i class="box"></i>ACUM</div>
  <div class="abs opt" style="top:851px"><i class="box on"></i>MAI TÂRZIU</div>
  <svg class="abs" style="left:206px;top:887px" width="18" height="18" viewBox="0 0 18 18"><circle cx="9" cy="10" r="6.5" fill="none" stroke="#888" stroke-width="1.5"/><path d="M9 6v4h3M2 4l3-2.5M16 4l-3-2.5" stroke="#888" stroke-width="1.5" fill="none"/></svg>
  <div class="abs time">13:30 <span style="font-size:9px">▼</span></div>

  <div class="abs label" style="left:518px;top:826px">ALTE INFORMAȚII</div>
  <div class="abs notes">Scrie aici orice informație care ar fi utilă în livrarea acestei comenzi.</div>

  <div class="abs rule" style="top:984px"></div>

  <div class="abs transport">COST TRANSPORT: 5 LEI</div>
  <div class="abs grand">COST TOTAL: <em>113 RON</em></div>
  <div class="abs send">TRIMITE COMANDA</div>
</main>

<footer class="abs site-footer">
  <nav class="abs foot-links">
    <a href="#">Contactează-ne</a><a href="#">Despre noi</a><a href="#">Parteneri noștri</a><a href="#">FAQ</a><a href="#">Devino partener</a>
  </nav>
  <div class="abs copy">Copyright © 2013 gustar.ro. Toate drepturile rezervate.</div>
</footer>
</body>
</html>
```